Looking for a modern, Professional business card design

We have a simple business card, but are looking for a more modern, professional look. A sample of the basic card is attached as well as the logo. We would also like to add that we offer:
Struggling with your finances?
- Learn to become debt free
- Discover the power of cash
- Control your money instead of it controlling you
Let us help you achieve a new level of financial freedom!
Also, we would like to have a "SPECIAL OFFER!: FREE 30 minute consultation"
Financial Planning

```html
<!DOCTYPE html>
<html lang="en">
<head>
<meta charset="utf-8">
<title>Brightpath Financial Coaching – Business Card</title>
<link rel="stylesheet" href="https://fonts.googleapis.com/css2?family=Archivo+Black&family=Roboto:wght@400;500&family=Roboto+Condensed:wght@400;700&display=swap">
<style>
  :root {
    --page-bg: #e4e0da;
    --card-top: #f3f2ee;
    --card-bottom: #e9e8e3;
    --card-edge: rgba(255,255,255,0.9);
    --band-dark: #1b1c1b;
    --band-mid: #2b2c2b;
    --green: #3e8a27;
    --green-bright: #5aab3b;
    --green-deep: #1f5f16;
    --ink: #1c1c1c;
    --text-light: #e6e6e6;
  }
  * { box-sizing: border-box; margin: 0; padding: 0; }
  html, body { width: 1200px; height: 969px; overflow: hidden; }
  body { background: var(--page-bg); position: relative; font-family: "Roboto", Arial, sans-serif; }

  .card {
    position: absolute; left: 350px; top: 47px; width: 500px; height: 875px;
    border-radius: 26px; overflow: hidden;
    background: linear-gradient(180deg, var(--card-top), var(--card-bottom));
    border: 2px solid var(--card-edge);
    box-shadow: 0 10px 30px rgba(0,0,0,0.15);
  }

  .brand {
    position: absolute; left: 34px; right: 24px; top: 0; height: 248px;
    display: flex; align-items: center; gap: 16px;
  }
  .brand-dot { width: 46px; height: 46px; border-radius: 50%; background: var(--green); flex: none; }
  .brand-name {
    font-family: "Archivo Black", Arial, sans-serif; font-size: 26px; line-height: 1.2;
    color: var(--green); text-transform: uppercase; white-space: nowrap;
  }

  .divider { position: absolute; left: 0; right: 0; top: 248px; height: 6px; background: var(--green); }

  .contact-band {
    position: absolute; left: 0; right: 0; top: 254px; height: 292px;
    background: linear-gradient(180deg, var(--band-mid), var(--band-dark));
    padding: 44px 0 0 34px;
  }
  .person-name { font-size: 34px; font-weight: 400; color: var(--green-bright); letter-spacing: 1px; text-transform: uppercase; }
  .person-role { margin-top: 8px; font-size: 23px; color: var(--text-light); }
  .contact-list { list-style: none; margin-top: 26px; }
  .contact-list li { display: flex; align-items: center; gap: 14px; font-size: 22px; color: var(--text-light); height: 35px; white-space: nowrap; }
  .contact-list svg { width: 22px; height: 22px; flex: none; }

  .offer-panel { position: absolute; left: 34px; right: 24px; top: 562px; }
  .offer-question {
    font-family: "Roboto Condensed", Arial, sans-serif; font-weight: 700; font-size: 25px;
    color: var(--green-deep); text-transform: uppercase;
  }
  .benefit-list { list-style: none; margin-top: 6px; }
  .benefit-list li {
    font-family: "Roboto Condensed", Arial, sans-serif; font-size: 19px; color: var(--ink);
    height: 36px; line-height: 36px; padding-left: 24px; position: relative;
  }
  .benefit-list li::before {
    content: ""; position: absolute; left: 4px; top: 15px; width: 7px; height: 7px; border-radius: 50%; background: var(--green-deep);
  }
  .offer-invite {
    margin-top: 6px; font-family: "Roboto Condensed", Arial, sans-serif; font-weight: 700; font-size: 15.5px;
    color: var(--ink); text-transform: uppercase; letter-spacing: -0.2px; white-space: nowrap;
  }
  .special-offer {
    margin-top: 24px; font-family: "Archivo Black", Arial, sans-serif; font-size: 45px; line-height: 1;
    color: var(--green-deep); text-transform: uppercase; white-space: nowrap;
  }
  .free-consult {
    margin-top: 8px; font-family: "Archivo Black", Arial, sans-serif; font-size: 23px;
    color: var(--ink); text-transform: uppercase; white-space: nowrap;
  }
  .free-consult .accent { color: var(--green-deep); }
</style>
</head>
<body>
  <article class="card">
    <header class="brand">
      <span class="brand-dot"></span>
      <span class="brand-name">Brightpath<br>Financial Coaching</span>
    </header>

    <div class="divider"></div>

    <section class="contact-band">
      <h1 class="person-name">Daniel R. Hayes</h1>
      <p class="person-role">Personal Financial Coach</p>
      <ul class="contact-list">
        <li>
          <svg viewBox="0 0 24 24" aria-hidden="true"><rect x="6" y="2" width="12" height="20" rx="2" fill="none" stroke="#5aab3b" stroke-width="2.4"/><circle cx="12" cy="18" r="1.3" fill="#5aab3b"/></svg>
          (555) 014-2290
        </li>
        <li>
          <svg viewBox="0 0 24 24" aria-hidden="true"><rect x="2" y="5" width="20" height="14" rx="1.5" fill="#5aab3b"/><path d="M2.5 6 L12 13 L21.5 6" fill="none" stroke="#1b1c1b" stroke-width="1.8"/></svg>
          daniel@steadyledgercoaching.com
        </li>
        <li>
          <svg viewBox="0 0 24 24" aria-hidden="true"><circle cx="12" cy="12" r="10" fill="#5aab3b"/><path d="M2 12 H22 M12 2 C7 7 7 17 12 22 M12 2 C17 7 17 17 12 22" fill="none" stroke="#1b1c1b" stroke-width="1.4"/></svg>
          www.steadyledgercoaching.com
        </li>
      </ul>
    </section>

    <section class="offer-panel">
      <h2 class="offer-question">Struggling with your finances?</h2>
      <ul class="benefit-list">
        <li>Learn to become debt free</li>
        <li>Discover the power of cash</li>
        <li>Control your money instead of it controlling you</li>
      </ul>
      <p class="offer-invite">Let us help you achieve a new level of financial freedom!</p>
      <p class="special-offer">Special Offer!</p>
      <p class="free-consult">Free <span class="accent">30 minute consultation</span></p>
    </section>
  </article>
</body>
</html>
```